Kelvara Pane Works Business Card

We need a business card design that is suitable for a Glazing Business. We Specialize in Repairing broken windows and doors and are a 24hr on call service. We manufacture Shower screens, Fly screens, Wardrobe doors, Security doors and grilles + mirrors. We stock a variety of mesh including Standard mesh, Pet resistant mesh, Tressmet & Clearweft. We would like to use a combination of Light Blue, Dark Blue, Black & White with perhaps a picture of glass breaking.

Industry/Entity Type

Business

Contact Information for Business Card

Narooma Glass Service60B Glasshouse Rocks RdNarooma NSW 2546PH / FAX - 02 44765210MOB - 0419682350 Andrewemail - kelvarapane@fenmail.example

Font styles to use
Serif

Colors
34a7d8
0255a3
ffffff

Requirements
Must have
• logo with picture of broken or cracked glass

```html
<!DOCTYPE html>
<html lang="en">
<head>
<meta charset="utf-8">
<title>Kelvara Pane Works – Business Card</title>
<link href="https://fonts.googleapis.com/css2?family=Lato:wght@400;700&display=swap" rel="stylesheet">
<style>
  :root {
    --bg: #e9e7e4;
    --card: #ffffff;
    --brand-blue: #0560e6;
    --accent-light: #34a7d8;
    --band-black: #000000;
    --ink: #1a1a1a;
    --on-blue: #ffffff;
  }
  * { margin: 0; padding: 0; box-sizing: border-box; }
  html, body { width: 1200px; height: 900px; overflow: hidden; }
  body {
    background: var(--bg);
    font-family: "Lato", Arial, sans-serif;
    position: relative;
  }
  .card {
    position: absolute;
    width: 589px;
    height: 364px;
    background: var(--card);
    overflow: hidden;
    box-shadow: 0 6px 18px rgba(0,0,0,0.18);
    transform-origin: top left;
  }
  .card--front { left: 77px; top: 33px; }
  .card--back { left: 388px; top: 505px; transform: scale(0.963); }

  .card__bands { position: absolute; inset: 0; width: 100%; height: 100%; }

  .brand {
    position: absolute;
    left: 110px;
    top: 64px;
    display: flex;
    align-items: center;
    gap: 10px;
    color: var(--brand-blue);
  }
  .brand__mark {
    width: 76px; height: 76px;
    background: var(--accent-light);
  }
  .brand__name { font-weight: 400; line-height: 1; }
  .brand__line1 { display: block; font-size: 48px; letter-spacing: 0.5px; }
  .brand__line2 { display: block; font-size: 27px; letter-spacing: 4px; margin-top: 4px; }

  .contact {
    position: absolute;
    right: 322px;
    top: 246px;
    list-style: none;
    color: var(--on-blue);
    font-size: 15.5px;
    text-align: right;
  }
  .contact li { height: 24.5px; display: flex; justify-content: flex-end; align-items: center; gap: 7px; }
  .contact svg { width: 12px; height: 12px; fill: var(--on-blue); }

  .person {
    position: absolute;
    left: 325px;
    top: 250px;
    color: var(--on-blue);
  }
  .person__name { font-size: 20px; font-weight: 700; margin-bottom: 14px; }
  .person__address { font-size: 16px; line-height: 25px; font-style: normal; }

  .services {
    position: absolute;
    list-style: none;
    color: var(--on-blue);
    font-size: 15.5px;
    font-weight: 700;
  }
  .services li { height: 26px; display: flex; align-items: center; gap: 8px; }
  .services li::before, .services--left li::after {
    content: ""; width: 8px; height: 8px; border-radius: 50%; background: var(--on-blue);
  }
  .services--left { right: 330px; top: 264px; }
  .services--left li { justify-content: flex-end; }
  .services--left li::before { display: none; }
  .services--right { left: 298px; top: 244px; }
</style>
</head>
<body>

<!-- Front of card -->
<section class="card card--front">
  <svg class="card__bands" viewBox="0 0 589 364" preserveAspectRatio="none" aria-hidden="true">
    <polygon points="0,200 408,200 383,225 0,225" fill="var(--band-black)"/>
    <polygon points="416,192 589,192 589,364 0,364 0,228 387,228" fill="var(--brand-blue)"/>
  </svg>

  <div class="brand">
    <span class="brand__mark"></span>
    <span class="brand__name">
      <span class="brand__line1">KELVARA</span>
      <span class="brand__line2">PANE WORKS</span>
    </span>
  </div>

  <ul class="contact">
    <li>02 48931067
      <svg viewBox="0 0 12 12"><path d="M2.5 0.8 4.3 3.2 3.2 4.6C4 6.2 5.8 8 7.4 8.8L8.8 7.7 11.2 9.5 10 11.3C5.5 11 1 6.5 0.7 2Z"/></svg></li>
    <li>02 48931067
      <svg viewBox="0 0 12 12"><rect x="1" y="4" width="10" height="7" rx="1"/><rect x="3" y="1" width="6" height="3" fill="none" stroke="#fff"/></svg></li>
    <li>0419682350
      <svg viewBox="0 0 12 12"><path d="M3 0h6a1 1 0 0 1 1 1v10a1 1 0 0 1-1 1H3a1 1 0 0 1-1-1V1a1 1 0 0 1 1-1zm0.5 1.5v7.5h5V1.5z"/></svg></li>
    <li>kelvarapane@fenmail.example
      <svg viewBox="0 0 12 12"><rect x="0.5" y="2" width="11" height="8"/><path d="M0.5 2 6 7 11.5 2" fill="none" stroke="#0560e6" stroke-width="1"/></svg></li>
  </ul>

  <div class="person">
    <p class="person__name">Malcolm</p>
    <address class="person__address">17C Tindale Ridge<br>Rd Tindale NSW 2551</address>
  </div>
</section>

<!-- Back of card -->
<section class="card card--back">
  <svg class="card__bands" viewBox="0 0 589 364" preserveAspectRatio="none" aria-hidden="true">
    <polygon points="0,198 408,198 383,223 0,223" fill="var(--band-black)"/>
    <polygon points="416,190 589,190 589,364 0,364 0,226 387,226" fill="var(--brand-blue)"/>
  </svg>

  <div class="brand">
    <span class="brand__mark"></span>
    <span class="brand__name">
      <span class="brand__line1">KELVARA</span>
      <span class="brand__line2">PANE WORKS</span>
    </span>
  </div>

  <ul class="services services--left">
    <li>Security doors</li>
    <li>Grilles + mirrors</li>
  </ul>
  <ul class="services services--right">
    <li>Shower screens</li>
    <li>Fly screens</li>
    <li>Wardrobe doors</li>
  </ul>
</section>

</body>
</html>
```